Business Card Design

We would like to re-design our business cards. Our Company - Qwinrel Turbochargers, rebuilds turbochargers and sells replacement parts. Our website is: http://www.qwinrelturbochargers-example.com
We just had our logo changed. I will attach the file. Looking for fresh new/modern business card. We like the colors red, black, white and silver. Black background looks attractive, but not a requirement. The final design should communicate reasonable/competitive prices, top quality and reliability of our products.
Updates
Project Deadline Extended
Reason: Need to finalize the info on the card. Currently working on changing address and email info. Want to make sure it is the correct one before accepting the final design. Unless, this is something that can be changed at a later time..??
Industry/Entity Type
Business
Contact Information for Business Card
QWINREL TURBOCHARGERS, LLC
20473 Harwick Lane NE
Massillon, OH 44647
Tel: +1-555-214-7390
Fax: +1-555-267-1842
info@QwinrelTurbochargers-example.com
Our current business card had the following highlights:
*We rebuild all Turbocharges for Automotive, Diesel and Industrial
*Precision Balancing and in-house turbocharger needs
*All Turbocharger replacement parts are made in USA / U.K.
Look and feel
Each slider illustrates characteristics of the customer's brand and the style your logo design should communicate.

```html
<!DOCTYPE html>
<html lang="en">
<head>
<meta charset="utf-8">
<title>Qwinrel Turbochargers – Business Card</title>
<link rel="stylesheet" href="https://fonts.googleapis.com/css2?family=Open+Sans:wght@400;600;700&display=swap">
<style>
  :root{
    --bg:#e9e6e1;
    --card-white:#ffffff;
    --card-grey:#eeeeee;
    --swoosh-grey:#e2e2e2;
    --red:#d6222c;
    --red-light:#ec5a60;
    --ink:#2b2b2b;
    --muted:#555555;
    --black:#141213;
    --black-soft:#2a2728;
  }
  *{box-sizing:border-box;margin:0;padding:0}
  html,body{width:1200px;height:1023px;overflow:hidden;background:var(--bg);font-family:"Open Sans",Arial,sans-serif}
  .canvas{position:relative;width:1200px;height:1023px}

  .card{position:absolute;width:630px;height:360px;border-radius:4px;overflow:hidden;box-shadow:0 8px 24px rgba(0,0,0,.18)}

  /* front */
  .card-front{left:70px;top:70px;background:linear-gradient(180deg,var(--card-white),var(--card-grey))}
  .card-front .band{position:absolute;left:0;top:0;width:630px;height:360px}
  .brand{position:absolute;left:60px;top:52px;display:flex;align-items:center;gap:12px}
  .brand-dot{width:18px;height:18px;border-radius:50%;background:var(--red)}
  .brand-name{font-weight:700;font-size:26px;color:var(--ink);letter-spacing:.2px}
  .person{position:absolute;left:60px;top:132px}
  .person-name{font-size:22px;color:var(--red);font-weight:400}
  .person-role{font-size:13px;color:var(--ink);margin-top:2px}
  .divider{position:absolute;left:272px;top:120px;width:2px;height:96px;background:var(--red)}
  .contacts{position:absolute;left:292px;top:118px;list-style:none}
  .contacts li{display:flex;align-items:center;gap:8px;font-size:13.5px;color:var(--ink);line-height:24px}
  .contacts svg{width:13px;height:13px;flex:none}
  .address{position:absolute;right:34px;bottom:22px;font-size:14px;color:#fff;letter-spacing:.3px}

  /* back */
  .card-back{left:500px;top:600px;background:linear-gradient(160deg,var(--black-soft),var(--black) 60%)}
  .back-brand{position:absolute;inset:0;display:flex;align-items:center;justify-content:center;gap:16px}
  .back-brand .brand-dot{width:26px;height:26px}
  .back-brand .brand-name{font-size:36px;color:var(--red)}
</style>
</head>
<body>
<main class="canvas">

  <section class="card card-front" aria-label="Business card front">
    <svg class="band" viewBox="0 0 630 360" aria-hidden="true">
      <path d="M0 312 C200 300 420 270 630 222 L630 360 L0 360 Z" fill="var(--swoosh-grey)"/>
      <path d="M0 330 C200 322 420 296 630 244 L630 360 L0 360 Z" fill="var(--red)"/>
      <path d="M0 322 C200 314 420 288 630 236 L630 244 C420 296 200 322 0 330 Z" fill="var(--red-light)"/>
    </svg>

    <div class="brand">
      <span class="brand-dot"></span>
      <span class="brand-name">Qwinrel Turbochargers</span>
    </div>

    <div class="person">
      <p class="person-name">Marlo Vestry</p>
      <p class="person-role">Director</p>
    </div>

    <div class="divider"></div>

    <ul class="contacts">
      <li><svg viewBox="0 0 16 16"><path d="M3 1l3 3-2 2c1 2 3 4 5 5l2-2 3 3-2 3C7 15 1 9 1 3z" fill="var(--red)"/></svg>+1-555-214-7390</li>
      <li><svg viewBox="0 0 16 16"><rect x="2" y="6" width="12" height="8" fill="var(--red)"/><rect x="4" y="2" width="8" height="4" fill="none" stroke="var(--red)" stroke-width="1.5"/></svg>+1-555-267-1842</li>
      <li><svg viewBox="0 0 16 16"><rect x="1" y="3" width="14" height="10" fill="var(--red)"/><path d="M1 3l7 6 7-6" fill="none" stroke="#fff" stroke-width="1.3"/></svg>info@QwinrelTurbochargers-example.com</li>
      <li><svg viewBox="0 0 16 16"><circle cx="8" cy="8" r="7" fill="var(--red)"/><path d="M1 8h14M8 1c-3 4-3 10 0 14M8 1c3 4 3 10 0 14" fill="none" stroke="#fff" stroke-width="1"/></svg>www.qwinrelturbochargers-example.com</li>
    </ul>

    <p class="address">4182 Dunmore Ave. NW North Harwick, Ohio</p>
  </section>

  <section class="card card-back" aria-label="Business card back">
    <div class="back-brand">
      <span class="brand-dot"></span>
      <span class="brand-name">Qwinrel Turbochargers</span>
    </div>
  </section>

</main>
</body>
</html>
```